executive development which breaks down traditional practices and thought processes

4 or 5 page website. Home page idea is fixed but needs creative execution to work {see attachment}, branding, as in corporate identity is in place and ready to go, (see attachment). Site needs to reflect the the market and typical participant, which are very high achievers up to and including Board Level Members in 'world leading company's'.

What we do is different, we are often copied, but without the success.

We require simple, slick impact, we have powerful messages that need to be supported by exquisite, simplistic design. We know we are the best out there and have kept our heads under water, but now is the time to start our expansion process.

We have copywriters briefed, and are liking what we read, so time to engage with designers who might like to 'wow' us, as well as our existing and potential clients.

Pages to include a standard landing/home page, about us, methodology, testimonials/awards and let's talk pages. Our philosophy is: opening minds to new ways of thinking, being, working and acting; to challenge long held business, management and leadership biases.

Our experiential learning technique is branded 'Tamarind' where we take people out of their comfort zone or into new & very different environments; to experience the way methodology and leadership techniques from uncomfortable encounters can be beneficial in big business strategic decision making, being more innovative and solving leadership & managerial challenges with new eyes (or a new perspective).

We will need to include video clips for awards we have won and testimonials from participants and company's alike. We work across the globe, the site needs to reflect this, without us looking like a huge corporate company, which we are not. We are small but pack a powerful punch, and that's the way we like it. Our clients don't see us as consultants or suppliers, more as the missing cog or the oil in the machine to get their executives to engage and deliver unorthodox thought processes which keep them at the forefront of their industries.

Both the copywriters and ourselves see typography being a crucial element to the impact of the site, so those designers with a passion in this area may well find our preference.

We are ready to go, good luck.

sorry guys missing the brief by a long way, we always said we were not looking for an off the shelf solution/concept which could be created on any 'sun pebble' like ortal and to be honest that's all we have received

Reason: designs miss the brief

Reason: We are not getting the desired simplistic landing page required.

```html
<!DOCTYPE html>
<html lang="en">
<head>
<meta charset="utf-8">
<title>Vantage Executive Development</title>
<link href="https://fonts.googleapis.com/css2?family=Ubuntu:ital,wght@0,400;0,500;0,700;1,400&display=swap" rel="stylesheet">
<style>
  :root {
    --brand-green: #45e21b;
    --brand-blue: #4000ff;
    --tick-green: #5b8c1f;
    --tagline-grey: #6b6f72;
    --ink: #111;
    --bg-light: #ffffff;
    --bg-edge: #dde2e5;
    --rule: #a9b2b8;
    --footer-text: #ffffff;
  }
  * { box-sizing: border-box; margin: 0; padding: 0; }
  html, body { width: 1200px; height: 946px; overflow: hidden; }
  body {
    position: relative;
    font-family: "Ubuntu", sans-serif;
    background: radial-gradient(ellipse 700px 520px at 600px 440px, var(--bg-light) 0%, #eef1f2 55%, var(--bg-edge) 100%);
  }
  .brand { position: absolute; left: 138px; top: 10px; }
  .brand-name {
    display: block;
    font-family: "Ubuntu", sans-serif;
    font-weight: 500;
    font-size: 104px;
    line-height: 1;
    letter-spacing: -2px;
    color: var(--brand-green);
  }
  .brand-tagline {
    position: absolute;
    left: 160px; top: 108px;
    font-size: 19px;
    color: var(--tagline-grey);
    white-space: nowrap;
  }
  .call {
    position: absolute;
    right: 139px; top: 84px;
    display: flex; align-items: center;
  }
  .call-icon { width: 34px; height: 44px; margin-right: 6px; }
  .call-divider { width: 1px; height: 54px; background: #c9ced2; margin-right: 6px; }
  .call-label { font-weight: 700; font-size: 16px; letter-spacing: 0.8px; color: var(--brand-blue); }
  .call-number { font-size: 24px; color: var(--ink); margin-top: 6px; }
  .header-rule {
    position: absolute; left: 138px; top: 166px; width: 924px; height: 6px;
    background: radial-gradient(ellipse at center, rgba(140,152,160,0.85) 0%, rgba(140,152,160,0.45) 60%, rgba(140,152,160,0) 100%);
    border-radius: 50%;
  }
  .definitions {
    position: absolute; left: 138px; top: 202px; width: 930px;
    list-style: none;
  }
  .definitions li {
    position: relative;
    padding-left: 35px;
    margin-bottom: 15.5px;
    font-style: italic;
    font-size: 20px;
    line-height: 30.5px;
    color: var(--brand-blue);
    word-break: break-all;
  }
  .definitions li span { display: block; }
  .tick { position: absolute; left: 2px; top: 8px; width: 21px; height: 19px; }
  .footer-rule {
    position: absolute; left: 138px; top: 836px; width: 924px; height: 5px;
    background: radial-gradient(ellipse at center, rgba(140,152,160,0.6) 0%, rgba(140,152,160,0) 100%);
  }
  .site-footer {
    position: absolute; left: 0; top: 841px; width: 1200px; height: 105px;
    background: var(--brand-blue);
    color: var(--footer-text);
    text-align: center;
    font-size: 16.5px;
  }
  .site-nav { margin-top: 26px; }
  .site-nav a { color: var(--footer-text); text-decoration: none; }
  .site-nav .sep { margin: 0 8px; }
  .copyright { margin-top: 18px; }
</style>
</head>
<body>
  <header>
    <div class="brand">
      <span class="brand-name">vantage</span>
      <span class="brand-tagline">Executive development</span>
    </div>
    <div class="call">
      <svg class="call-icon" viewBox="0 0 34 44" aria-hidden="true">
        <path d="M2 10 Q17 -2 32 10 L29 15 Q17 7 5 15 Z" fill="#222"/>
        <g fill="#333">
          <circle cx="11" cy="19" r="2.2"/><circle cx="17" cy="19" r="2.2"/><circle cx="23" cy="19" r="2.2"/>
          <circle cx="11" cy="25" r="2.2"/><circle cx="17" cy="25" r="2.2"/><circle cx="23" cy="25" r="2.2"/>
          <circle cx="11" cy="31" r="2.2"/><circle cx="17" cy="31" r="2.2"/><circle cx="23" cy="31" r="2.2"/>
        </g>
        <g fill="#aaa">
          <circle cx="11" cy="37" r="2"/><circle cx="17" cy="37" r="2"/><circle cx="23" cy="37" r="2"/>
        </g>
      </svg>
      <div class="call-divider"></div>
      <div>
        <div class="call-label">CALL US TODAY:</div>
        <div class="call-number">123-456-7890</div>
      </div>
    </div>
    <div class="header-rule"></div>
  </header>

  <main>
    <ul class="definitions">
      <li><svg class="tick" viewBox="0 0 21 19"><path d="M1 10 L5 8 L8 13 Q13 4 21 0 Q13 7 8 19 Z" fill="var(--tick-green)"/></svg>
        <span>n</span><span>The Act Or An Instance Of Looking For Or Seeking; Sear</span></li>
      <li><svg class="tick" viewBox="0 0 21 19"><path d="M1 10 L5 8 L8 13 Q13 4 21 0 Q13 7 8 19 Z" fill="var(--tick-green)"/></svg>
        <span>ch: a</span><span>quest fordiamonds.</span><span>(Historical Terms) (in medieval romance) an expedition by aknightor company of knightsto accomplish some prescribed task, such asfinding the Holy Grail</span></li>
      <li><svg class="tick" viewBox="0 0 21 19"><path d="M1 10 L5 8 L8 13 Q13 4 21 0 Q13 7 8 19 Z" fill="var(--tick-green)"/></svg>
        <span>The Object Of A Search; Goal Or Target: My Quest Is The Treasure Ofthe King.</span></li>
      <li><svg class="tick" viewBox="0 0 21 19"><path d="M1 10 L5 8 L8 13 Q13 4 21 0 Q13 7 8 19 Z" fill="var(--tick-green)"/></svg>
        <span>A Collection Of Alms</span></li>
      <li><svg class="tick" viewBox="0 0 21 19"><path d="M1 10 L5 8 L8 13 Q13 4 21 0 Q13 7 8 19 Z" fill="var(--tick-green)"/></svg>
        <span>vb (mainly intr)</span><span>(foll By: For Or After) To Go In Search (of)</span></li>
      <li><svg class="tick" viewBox="0 0 21 19"><path d="M1 10 L5 8 L8 13 Q13 4 21 0 Q13 7 8 19 Z" fill="var(--tick-green)"/></svg>
        <span>(historical Terms) To Go On A Quest</span></li>
      <li><svg class="tick" viewBox="0 0 21 19"><path d="M1 10 L5 8 L8 13 Q13 4 21 0 Q13 7 8 19 Z" fill="var(--tick-green)"/></svg>
        <span>(hunting) (of Gun Dogs Or Hounds)</span><span>A. To Search For Game</span><span>B. To Bay When In Pursuit Of Game</span></li>
      <li><svg class="tick" viewBox="0 0 21 19"><path d="M1 10 L5 8 L8 13 Q13 4 21 0 Q13 7 8 19 Z" fill="var(--tick-green)"/></svg>
        <span>To Collect Alms</span></li>
      <li><svg class="tick" viewBox="0 0 21 19"><path d="M1 10 L5 8 L8 13 Q13 4 21 0 Q13 7 8 19 Z" fill="var(--tick-green)"/></svg>
        <span>(also Tr) To Go In Search Of (a Thing); Seek Or Pursue</span></li>
    </ul>
    <div class="footer-rule"></div>
  </main>

  <footer class="site-footer">
    <nav class="site-nav">
      <a href="#">Home</a><span class="sep">|</span><a href="#">About Us</a><span class="sep">|</span><a href="#">Methodology</a><span class="sep">|</span><a href="#">Testimonials/awards</a><span class="sep">|</span><a href="#">Let's Talk</a>
    </nav>
    <p class="copyright">© 2014 vantageexecutivedevelopment. All right reserved</p>
  </footer>
</body>
</html>
```